Business Card Design

New business card design

Target Market(s)

Residential & Commercial Property Managers

Industry/Entity Type

Plumbing Services

Contact Information for Business Card

Name - Rowan Keddle, title - Director, Phone Number - 0431 286 517, email - rowan@tbk-plumbing.com.au, Company ABN - 73 215 904 386,

Font styles to use
Sans Serif

Colors
0054AA
0677BA
7BADD7
CADEEF
E8F1F8

```html
<!DOCTYPE html>
<html lang="en">
<head>
<meta charset="utf-8">
<title>TBK Plumbing Services – Business Card</title>
<link rel="stylesheet" href="https://fonts.googleapis.com/css2?family=Poppins:wght@300;400;600&display=swap">
<style>
  :root {
    --stage: #222222;
    --card-dark: #1a2029;
    --card-dark-edge: #141a22;
    --card-blue: #29a9e1;
    --card-blue-deep: #1f8fc4;
    --accent: #2f9bd6;
    --ink-light: #f2f4f6;
    --ink-muted: #8a8f95;
    --ink-soft: #c9ced4;
  }
  * { box-sizing: border-box; margin: 0; padding: 0; }
  html, body {
    width: 1200px; height: 780px; overflow: hidden;
    background: var(--stage);
    font-family: "Poppins", sans-serif;
  }
  .canvas {
    position: relative; width: 1200px; height: 780px;
    display: flex; align-items: center; justify-content: center; gap: 48px;
  }
  .card {
    position: relative; width: 525px; height: 300px;
    border-radius: 22px; overflow: hidden;
    box-shadow: 0 18px 40px rgba(0,0,0,.55);
  }
  /* Front: contact side */
  .card--front {
    background: var(--card-dark);
    display: flex; flex-direction: column; align-items: center;
    padding-top: 42px;
  }
  .card--front::before {
    content: ""; position: absolute; inset: 0;
    background: linear-gradient(160deg, transparent 30%, rgba(255,255,255,.045) 45%, transparent 60%);
    pointer-events: none;
  }
  .brand {
    display: flex; align-items: center; gap: 10px;
  }
  .brand__dot {
    width: 12px; height: 12px; border-radius: 50%;
    background: var(--accent);
  }
  .brand__name {
    font-weight: 300; font-size: 26px; letter-spacing: .04em;
    color: var(--ink-light); line-height: 1;
  }
  .person { margin-top: 30px; text-align: center; }
  .person__name {
    font-size: 24px; line-height: 1.1; font-weight: 300; color: var(--ink-muted);
  }
  .person__first { font-weight: 600; color: var(--accent); }
  .person__title {
    font-size: 12px; color: var(--ink-light); margin-top: 2px;
  }
  .abn {
    font-size: 12px; color: var(--accent); margin-top: 10px; letter-spacing: .02em;
  }
  .contacts {
    list-style: none; margin-top: 16px;
    display: flex; flex-direction: column; gap: 6px;
  }
  .contacts__item {
    display: flex; align-items: center; gap: 10px;
    font-size: 11.5px; font-weight: 300; color: var(--ink-soft);
  }
  .contacts__icon {
    width: 16px; height: 16px; border-radius: 4px;
    background: var(--accent); display: grid; place-items: center;
    transform: rotate(45deg);
  }
  .contacts__icon svg { transform: rotate(-45deg); }

  /* Back: brand side */
  .card--back {
    background: linear-gradient(180deg, var(--card-blue) 0%, var(--card-blue) 80%, var(--card-blue-deep) 100%);
    display: flex; align-items: center; justify-content: center;
  }
  .card--back .brand__name {
    font-size: 40px; color: #1b7fb5;
  }
  .card--back .brand__dot {
    width: 18px; height: 18px; background: #f2f8fc;
  }
</style>
</head>
<body>
<main class="canvas">
  <section class="card card--front" aria-label="Business card front">
    <div class="brand">
      <span class="brand__name">TBK Plumbing Services</span>
      <span class="brand__dot"></span>
    </div>
    <div class="person">
      <p class="person__name"><span class="person__first">Rowan</span> Keddle</p>
      <p class="person__title">Director</p>
    </div>
    <p class="abn">ABN - 73 215 904 386</p>
    <ul class="contacts">
      <li class="contacts__item">
        <span class="contacts__icon">
          <svg width="9" height="9" viewBox="0 0 24 24" fill="#fff"><path d="M6.6 10.8a15 15 0 0 0 6.6 6.6l2.2-2.2c.3-.3.7-.4 1-.2 1.1.4 2.3.6 3.6.6.6 0 1 .4 1 1V20c0 .6-.4 1-1 1A17 17 0 0 1 3 4c0-.6.4-1 1-1h3.5c.6 0 1 .4 1 1 0 1.3.2 2.5.6 3.6.1.3 0 .7-.2 1z"/></svg>
        </span>
        0431 286 517
      </li>
      <li class="contacts__item">
        <span class="contacts__icon">
          <svg width="9" height="9" viewBox="0 0 24 24" fill="none" stroke="#fff" stroke-width="2.4"><circle cx="12" cy="12" r="9"/><path d="M3 12h18M12 3c3 3 3 15 0 18M12 3c-3 3-3 15 0 18"/></svg>
        </span>
        www.tbk-plumbing.com.au
      </li>
      <li class="contacts__item">
        <span class="contacts__icon">
          <svg width="9" height="9" viewBox="0 0 24 24" fill="none" stroke="#fff" stroke-width="2.4"><rect x="3" y="5" width="18" height="14" rx="2"/><path d="M3 7l9 6 9-6"/></svg>
        </span>
        rowan@tbk-plumbing.com.au
      </li>
    </ul>
  </section>

  <section class="card card--back" aria-label="Business card back">
    <div class="brand">
      <span class="brand__name">TBK Plumbing Services</span>
      <span class="brand__dot"></span>
    </div>
  </section>
</main>
</body>
</html>
```